Business Card Design needed for start up company Halvora

In need of a new business card designed for a start up company based in Sydney, Halvora is a new start up innovative Company, our mission it to make property accessible for everyday Australian and to become the leading Real Estate platform in Australia. We want it to be fresh and clean.

Industry/Entity Type

Financial

Contact Information for Business Card

Section for Name
Section for Title

HALVORA - The Strength of Pooling
Mobile:
Direct:

Font styles to use
Sans Serif

Colors
33a6d7
0692cd
0255a3
ffffff

Requirements
Must have
• Logo, all business card details

```html
<!DOCTYPE html>
<html lang="en">
<head>
<meta charset="utf-8">
<title>Halvora Business Card</title>
<link rel="stylesheet" href="https://fonts.googleapis.com/css2?family=Exo+2:wght@400;500;700;800&display=swap">
<style>
  :root {
    --sky: #4fbbea;
    --blue: #33a6d7;
    --navy: #1f3f9a;
    --ink: #3a3a3c;
    --paper: #ffffff;
    --backdrop: #2e2f31;
  }
  * { box-sizing: border-box; margin: 0; padding: 0; }
  html, body {
    width: 1200px; height: 1000px; overflow: hidden;
    background: var(--backdrop);
    font-family: "Exo 2", sans-serif;
  }
  .stage { position: relative; width: 1200px; height: 1000px; }
  .card {
    position: absolute; width: 700px; height: 400px;
    border-radius: 22px; overflow: hidden;
  }
  .card-back {
    left: 250px; top: 60px;
    background: var(--sky);
    display: flex; align-items: center; justify-content: center;
  }
  .card-front {
    left: 250px; top: 540px;
    background: var(--paper);
  }
  .wordmark {
    font-family: "Exo 2", sans-serif; font-weight: 700;
    letter-spacing: 0.5px; line-height: 1; white-space: nowrap;
  }
  .card-back .wordmark { font-size: 64px; color: var(--paper); }
  .card-front .wordmark {
    position: absolute; right: 60px; top: 120px;
    font-size: 40px; color: var(--navy);
  }

  .card-art { position: absolute; inset: 0; }

  .name-tab {
    position: absolute; left: 0; top: 44px; width: 8px; height: 30px;
    background: var(--sky);
  }
  .person { position: absolute; left: 28px; top: 40px; }
  .person-name {
    font-size: 27px; font-weight: 800; color: var(--ink); letter-spacing: 1.5px;
  }
  .person-title {
    font-size: 19px; font-weight: 500; color: var(--blue); margin-top: -2px;
  }
  .contacts {
    position: absolute; left: 20px; top: 132px;
    list-style: none; font-size: 16px; color: var(--ink); line-height: 23px;
  }
  .contacts li { display: flex; align-items: center; gap: 10px; }
  .contacts svg { width: 13px; height: 13px; fill: var(--sky); flex: none; }
  .contacts .accent { color: var(--blue); }

  .address {
    position: absolute; right: 70px; top: 268px; text-align: right;
    font-size: 17px; color: var(--ink); line-height: 23px; letter-spacing: 0.5px;
  }
  .address-pin {
    position: absolute; right: 36px; top: 284px; width: 20px; height: 20px;
  }
  .band-url {
    position: absolute; right: 40px; top: 348px;
    font-size: 20px; font-weight: 500; color: var(--paper); letter-spacing: 1px;
  }
</style>
</head>
<body>
<main class="stage">
  <section class="card card-back" aria-label="Card back">
    <p class="wordmark">Halvora</p>
  </section>

  <section class="card card-front" aria-label="Card front">
    <svg class="card-art" viewBox="0 0 700 400" width="700" height="400" aria-hidden="true">
      <line x1="28" y1="110" x2="250" y2="110" stroke="#33a6d7" stroke-width="1.5"/>
      <line x1="28" y1="248" x2="600" y2="248" stroke="#33a6d7" stroke-width="1.5"/>
      <polygon points="0,326 448,326 444,332 0,332" fill="#4fbbea"/>
      <polygon points="0,342 452,342 484,314 700,314 700,400 0,400" fill="#1f3f9a"/>
    </svg>

    <div class="name-tab"></div>
    <div class="person">
      <div class="person-name">DANIEL REYES</div>
      <div class="person-title">Director</div>
    </div>

    <ul class="contacts">
      <li><svg viewBox="0 0 16 16"><path d="M3.6 1.2l2.3 2.6-1.2 1.9c.9 2 2.4 3.5 4.4 4.4l1.9-1.2 2.6 2.3-1.3 2.6C7.6 13.7 2.3 8.4 1 3.1z"/></svg><span>02 8041 3927</span></li>
      <li><svg viewBox="0 0 16 16"><path d="M4 0h8a1 1 0 011 1v14a1 1 0 01-1 1H4a1 1 0 01-1-1V1a1 1 0 011-1zm1 2v10h6V2zm3 11a1 1 0 100 2 1 1 0 000-2z"/></svg><span>0412 558 201</span></li>
      <li><svg viewBox="0 0 16 16"><path d="M0 3h16v10H0zm1.5 1.2L8 9l6.5-4.8V4h-13z"/></svg><span>daniel@halvora.com</span></li>
      <li><svg viewBox="0 0 16 16"><path d="M8 0a8 8 0 100 16A8 8 0 008 0zm5.9 7h-2.6a12 12 0 00-1-4.8A6 6 0 0113.9 7zM8 2c.7.8 1.3 2.7 1.4 5H6.6C6.7 4.7 7.3 2.8 8 2zM5.7 2.2a12 12 0 00-1 4.8H2.1a6 6 0 013.6-4.8zM2.1 9h2.6c.1 1.8.4 3.5 1 4.8A6 6 0 012.1 9zM8 14c-.7-.8-1.3-2.7-1.4-5h2.8c-.1 2.3-.7 4.2-1.4 5zm2.3-.2a12 12 0 001-4.8h2.6a6 6 0 01-3.6 4.8z"/></svg><span>www.<span class="accent">halvora</span>.com</span></li>
    </ul>

    <p class="wordmark">Halvora</p>

    <p class="address">18 Harbour Lane,<br>Sydney, 2000</p>
    <svg class="address-pin" viewBox="0 0 20 20" aria-hidden="true">
      <path d="M2 12l16-6-7 12-2-5z" fill="none" stroke="#33a6d7" stroke-width="1.4" stroke-linejoin="round"/>
    </svg>

    <p class="band-url">www.halvora.com</p>
  </section>
</main>
</body>
</html>
```